Retail Seafood business needs package/label design

In need of packaging/label design for multiple seafood products such as sword fish, halibut, cod fish, scallops, mahi, catfish, and lobster tails

```html
<!DOCTYPE html>
<html lang="en">
<head>
<meta charset="utf-8">
<title>Tidewell Market – Salmon Label</title>
<link rel="stylesheet" href="https://fonts.googleapis.com/css2?family=Bebas+Neue&family=Caveat+Brush&family=Montserrat:wght@500;600;700&display=swap">
<style>
  :root {
    --mint: #d4f7e6;
    --teal: #5ea8bd;
    --sea-light: #97cfdb;
    --navy: #2f4379;
    --navy-deep: #2a3c6e;
    --cream: #efe6dc;
    --coral: #cf7d5a;
    --strip: #77b4c9;
    --ink: #2f4379;
  }
  * { box-sizing: border-box; margin: 0; padding: 0; }
  html, body { width: 1200px; height: 1200px; overflow: hidden; }
  body { background: var(--mint); font-family: "Montserrat", sans-serif; }

  .label {
    position: absolute; left: 320px; top: 50px;
    width: 560px; height: 1100px;
    background: var(--teal);
  }
  .label-shapes { position: absolute; inset: 0; }

  .brand-badge {
    position: absolute; left: 148px; top: 35px; width: 264px; height: 264px;
    display: flex; flex-direction: column; align-items: center; justify-content: center;
    text-align: center; color: var(--cream);
  }
  .brand-badge .brand-name {
    font-weight: 700; font-size: 27px; letter-spacing: 2px; line-height: 1.1;
  }
  .brand-badge .tagline {
    margin-top: 14px; font-size: 8.5px; font-weight: 500; letter-spacing: 1.3px; line-height: 1.35;
    text-transform: uppercase;
  }

  .product-title {
    position: absolute; left: 46px; width: 468px; top: 372px;
    text-align: center; color: var(--cream);
    font-family: "Bebas Neue", sans-serif; font-size: 80px; line-height: 0.82; letter-spacing: 2px;
  }
  .product-type {
    position: absolute; left: 46px; width: 468px; top: 535px;
    text-align: center; color: var(--sea-light);
    font-family: "Caveat Brush", cursive; font-size: 50px; line-height: 1;
  }

  .detail {
    position: absolute; left: 46px; width: 468px; text-align: center;
    text-transform: uppercase; color: var(--ink); font-weight: 500;
  }
  .detail.weight { top: 658px; font-size: 8.5px; letter-spacing: 1.3px; }
  .detail.story { top: 702px; font-size: 10px; letter-spacing: 1.6px; line-height: 1.22; }
  .detail.tags { top: 773px; font-size: 9.5px; letter-spacing: 1.5px; color: var(--coral); }

  .store-info {
    position: absolute; left: 0; width: 560px; top: 893px;
    text-align: center; color: var(--cream);
  }
  .store-info .brand-name { font-weight: 700; font-size: 30px; letter-spacing: 2px; margin-bottom: 10px; }
  .store-info address { font-style: normal; font-size: 12.5px; font-weight: 600; letter-spacing: 1.4px; line-height: 1.62; text-transform: uppercase; }
  .store-info .web { text-transform: none; letter-spacing: 0.6px; }

  .social-strip {
    position: absolute; left: 0; top: 1049px; width: 560px; height: 51px;
    display: flex; justify-content: space-around; align-items: center;
    padding: 0 20px; color: var(--cream); font-size: 12px; font-weight: 500;
  }
  .social-item { display: flex; align-items: center; gap: 6px; }
  .social-item .dot { width: 12px; height: 12px; border-radius: 50%; background: var(--navy); }
</style>
</head>
<body>
<main class="label">
  <svg class="label-shapes" width="560" height="1100" viewBox="0 0 560 1100" aria-hidden="true">
    <rect x="46" y="67" width="468" height="760" fill="var(--sea-light)"/>
    <rect x="46.5" y="67.5" width="467" height="760" fill="none" stroke="var(--coral)" stroke-width="1"/>
    <circle cx="280" cy="167" r="132" fill="var(--navy)"/>
    <circle cx="280" cy="167" r="122" fill="none" stroke="var(--sea-light)" stroke-width="1"/>
    <path fill="var(--navy)" d="M46 325 q6.5 -7 13 0 t13 0 t13 0 t13 0 t13 0 t13 0 t13 0 t13 0 t13 0 t13 0 t13 0 t13 0 t13 0 t13 0 t13 0 t13 0 t13 0 t13 0 t13 0 t13 0 t13 0 t13 0 t13 0 t13 0 t13 0 t13 0 t13 0 t13 0 t13 0 t13 0 t13 0 t13 0 t13 0 t13 0 t13 0 t13 0 L514 626 q-6.5 7 -13 0 t-13 0 t-13 0 t-13 0 t-13 0 t-13 0 t-13 0 t-13 0 t-13 0 t-13 0 t-13 0 t-13 0 t-13 0 t-13 0 t-13 0 t-13 0 t-13 0 t-13 0 t-13 0 t-13 0 t-13 0 t-13 0 t-13 0 t-13 0 t-13 0 t-13 0 t-13 0 t-13 0 t-13 0 t-13 0 t-13 0 t-13 0 t-13 0 t-13 0 t-13 0 t-13 0 Z"/>
    <line x1="66" y1="690" x2="494" y2="690" stroke="var(--coral)" stroke-width="0.8" opacity="0.6"/>
    <line x1="66" y1="757" x2="494" y2="757" stroke="var(--coral)" stroke-width="0.8" opacity="0.6"/>
    <path fill="var(--navy-deep)" d="M0 820 q7 -7 14 0 t14 0 t14 0 t14 0 t14 0 t14 0 t14 0 t14 0 t14 0 t14 0 t14 0 t14 0 t14 0 t14 0 t14 0 t14 0 t14 0 t14 0 t14 0 t14 0 t14 0 t14 0 t14 0 t14 0 t14 0 t14 0 t14 0 t14 0 t14 0 t14 0 t14 0 t14 0 t14 0 t14 0 t14 0 t14 0 t14 0 t14 0 t14 0 t14 0 L560 1049 L0 1049 Z"/>
    <rect x="0" y="1049" width="560" height="51" fill="var(--strip)"/>
  </svg>

  <div class="brand-badge">
    <div class="brand-name">TIDEWELL<br>MARKET</div>
    <p class="tagline">The Midwest's source of<br>seafood &amp; produce<br>for over 15 years</p>
  </div>

  <h1 class="product-title">Salmon,<br>Faroe Islands</h1>
  <p class="product-type">fresh seafood</p>

  <p class="detail weight">4-5 lb average per fillet</p>
  <p class="detail story">Categorized as the best salmon you can eat.<br>The Faroe Islands are known for producing<br>the world's finest Atlantic salmon.<br>Naturally raised free of antibiotics.</p>
  <p class="detail tags">Sashimi grade &nbsp;•&nbsp; Sustainably farmed &nbsp;•&nbsp; Fresh</p>

  <div class="store-info">
    <div class="brand-name">TIDEWELL MARKET</div>
    <address>
      118 W. Harbor Lane<br>
      Portside, IL 60455<br>
      555-014-2210<br>
      <span class="web">www.tidewellmarket.com/</span>
    </address>
  </div>

  <div class="social-strip">
    <span class="social-item"><span class="dot"></span>tidewell.market</span>
    <span class="social-item"><span class="dot"></span>@tidewellmarket</span>
    <span class="social-item"><span class="dot"></span>@tidewellmarket</span>
  </div>
</main>
</body>
</html>
```